Computer consultant business card

Bexil Software is a newly started computer consulting company. It's a small one-man company that provides mostly Vornix applications but also websites in collaboration with designers. I'm running this company on the side of full time university studies.

I want the final design to be clean and memorable. Be creative! :)

Some inspiration:
http://www.pixelmarta.com/design/48317
http://www.pixelmarta.com/design/2739164/business-card-design-by-frostlynk
http://www.pixelmarta.com/design/604281/business-card-design-by-koralind-vestrabanu

See attachment for my company logo.
Updates

I would like to thank everyone for submitting! I'll need a couple of days to review and ultimately select a design.

Target Market(s)

Non-technical entrepreneurs and small companies.

Industry/Entity Type

University

Requirements
Must have
• My company logo.
In any way, both colors from my logo.
First- and last name, e-mail and phone number.
Double-sided design.
Nice to have
• Something creative with the symbol in my logo

```html
<!DOCTYPE html>
<html lang="en">
<head>
<meta charset="utf-8">
<title>Bexil Software – Business Card</title>
<link rel="stylesheet" href="https://fonts.googleapis.com/css2?family=Nunito:wght@700&family=Cinzel:wght@400;600&family=Arimo:wght@400&display=swap">
<style>
  :root {
    --canvas-bg: #e6e7ea;
    --card-white: #ffffff;
    --brand-blue: #3e74b9;
    --brand-blue-light: #6d9fd4;
    --brand-grey: #48474c;
    --contact-white: #f4f7fb;
  }
  * { box-sizing: border-box; margin: 0; padding: 0; }
  html, body {
    width: 1200px; height: 900px; overflow: hidden;
    background: var(--canvas-bg);
  }
  .canvas {
    position: relative; width: 1200px; height: 900px;
  }
  .card {
    position: absolute; left: 250px;
    width: 700px; height: 400px;
    background: var(--card-white);
    box-shadow: 0 6px 18px rgba(0,0,0,.18);
    overflow: hidden;
  }
  .card--front { top: 40px; }
  .card--back { top: 470px; }
  .card__art { position: absolute; inset: 0; width: 100%; height: 100%; }

  .brand {
    position: absolute; left: 150px; top: 110px;
    display: flex; align-items: center; gap: 22px;
  }
  .brand__dot {
    width: 74px; height: 74px; border-radius: 50%;
    background: var(--brand-blue);
  }
  .brand__name {
    font-family: "Nunito", sans-serif; font-weight: 700;
    font-size: 96px; line-height: 1; letter-spacing: 1px;
    color: var(--brand-grey);
  }

  .holder {
    position: absolute; left: 48px; top: 92px;
    font-family: "Cinzel", serif; color: var(--brand-blue);
  }
  .holder__name { font-size: 30px; font-weight: 600; letter-spacing: 1px; }
  .holder__role { margin-top: 6px; font-size: 16px; letter-spacing: 4px; }

  .contact {
    position: absolute; right: 34px; top: 92px;
    list-style: none;
    font-family: "Arimo", sans-serif; font-size: 17px;
    color: var(--contact-white);
  }
  .contact__item {
    display: flex; align-items: center; gap: 12px; margin-bottom: 9px;
  }
  .contact__icon { width: 15px; height: 15px; flex: none; }
</style>
</head>
<body>
<main class="canvas">

  <section class="card card--front" aria-label="Card front">
    <svg class="card__art" viewBox="0 0 700 400" preserveAspectRatio="none" aria-hidden="true">
      <defs>
        <linearGradient id="bandFront" x1="0" y1="0" x2="1" y2="1">
          <stop offset="0" stop-color="#4a80c2"/>
          <stop offset="1" stop-color="#3e74b9"/>
        </linearGradient>
      </defs>
      <path d="M700 0 L640 0 C560 90 420 250 120 330 C70 342 30 348 0 350 L0 400 L700 400 Z" fill="url(#bandFront)"/>
      <path d="M610 0 L590 0 C510 120 370 240 130 300 C360 270 520 150 610 0 Z" fill="var(--brand-blue-light)"/>
      <path d="M0 362 C220 350 420 300 560 210 C420 330 200 385 0 380 Z" fill="#ffffff"/>
      <path d="M60 370 C260 360 420 320 520 260 C400 340 240 375 60 370 Z" fill="var(--brand-blue)"/>
    </svg>
    <div class="brand">
      <span class="brand__dot"></span>
      <span class="brand__name">bexil</span>
    </div>
  </section>

  <section class="card card--back" aria-label="Card back">
    <svg class="card__art" viewBox="0 0 700 400" preserveAspectRatio="none" aria-hidden="true">
      <defs>
        <linearGradient id="bandBack" x1="0" y1="0" x2="1" y2="1">
          <stop offset="0" stop-color="#4f86c6"/>
          <stop offset="1" stop-color="#3a6fb3"/>
        </linearGradient>
      </defs>
      <path d="M700 0 L380 0 C460 40 480 120 450 200 C420 280 330 350 240 400 L700 400 Z" fill="url(#bandBack)"/>
      <path d="M360 0 L345 0 C430 70 430 200 330 300 C260 360 160 390 60 400 L110 400 C230 380 360 320 420 220 C470 140 440 50 360 0 Z" fill="var(--brand-blue)"/>
      <path d="M0 400 C140 380 260 330 330 260 C270 350 150 395 40 400 Z" fill="var(--brand-blue-light)"/>
    </svg>
    <div class="holder">
      <p class="holder__name">Elias Marren</p>
      <p class="holder__role">DIRECTOR</p>
    </div>
    <ul class="contact">
      <li class="contact__item">
        <svg class="contact__icon" viewBox="0 0 16 16" aria-hidden="true"><path d="M3 1h3l1 4-2 1.5a9 9 0 0 0 4.5 4.5L11 9l4 1v3a2 2 0 0 1-2 2A12 12 0 0 1 1 3a2 2 0 0 1 2-2z" fill="currentColor"/></svg>
        +(000) 1234 5678
      </li>
      <li class="contact__item">
        <svg class="contact__icon" viewBox="0 0 16 16" aria-hidden="true"><rect x="2" y="6" width="12" height="9" fill="currentColor"/><rect x="4" y="1" width="8" height="5" fill="none" stroke="currentColor" stroke-width="1.5"/></svg>
        +(000) 1234 5679
      </li>
      <li class="contact__item">
        <svg class="contact__icon" viewBox="0 0 16 16" aria-hidden="true"><rect x="1" y="3" width="14" height="10" fill="none" stroke="currentColor" stroke-width="1.5"/><path d="M1 3l7 6 7-6" fill="none" stroke="currentColor" stroke-width="1.5"/></svg>
        email@yourdomain.com
      </li>
      <li class="contact__item">
        <svg class="contact__icon" viewBox="0 0 16 16" aria-hidden="true"><circle cx="8" cy="8" r="7" fill="currentColor"/></svg>
        www.yourwebsite.com
      </li>
    </ul>
  </section>

</main>
</body>
</html>
```